Family business needs stationery redesign with new logo

Family owned company, established in 1987 wanting a brand 'refresh'. We are an electrical, refrigeration and construction company based in the Barkly Region Northern Territory, Australia. We have a new logo we would like to use which is uploaded along with our current letterhead and email signature. We are also dropping the word 'contractors' so please do not include this on any designs. Please note also, the 'orange' color used in our logo and designs should be Northern Territory red ochre which is as follows:

RGB (Hex): #C75B12
PantoneĀ® 159 C
CMYK: 1 / 74 / 100 / 7

We are needing our stationery redesigned using our new logo. Please include letterheads, business cards, envelopes, and email signatures.

We currently use our business letterheads for quotations, invoices, letters, HR matters, and internal memos.

We also need a separate simplified letterhead for internal paperwork such as employee leave forms, meeting agendas, and meeting minutes etc.

Reason: Needing more submissions of full package designs. We are wanting all our stationery, including business cards, letterheads, email signatures, envelopes, etc to be cohesive. We also require ALL the information, as supplied on our template letterhead, to be included on the new letterhead designs. including electrical license no.etc Thank you, R&W

Reason: needing more time as work has got in the way of looking over designs. A lot of designs not meeting the brief/criteria.

Industry/Entity Type

Business

Colors
0355a3
f37122

Requirements
Must have
• The 'orange' color used in the designs should be Northern Territory red ochre which is as follows:
• RGB (Hex): #C75B12
• PantoneĀ® 159 C
• CMYK: 1 / 74 / 100 / 7
• ***MUST INCLUDE ALL INFORMATION THAT IS ON OUR CURRENT LETTERHEAD***
Should not have
• Please do not include the word 'contractors'

```html
<!DOCTYPE html>
<html lang="en">
<head>
<meta charset="utf-8">
<title>R&amp;W Business Card</title>
<link href="https://fonts.googleapis.com/css2?family=Arimo:wght@400;700&display=swap" rel="stylesheet">
<style>
  :root {
    --backdrop: #e6e3df;
    --card-light: #f1f2f3;
    --navy-deep: #0b1440;
    --navy-mid: #24336e;
    --navy-text: #0f1a4a;
    --ochre: #c75b12;
    --body-text: #222a3a;
    --white: #ffffff;
  }
  * { margin: 0; padding: 0; box-sizing: border-box; }
  html, body {
    width: 1200px;
    height: 969px;
    overflow: hidden;
    background: var(--backdrop);
    font-family: "Arimo", Arial, sans-serif;
  }
  .business-card {
    position: absolute;
    left: 100px;
    top: 224px;
    width: 1000px;
    height: 520px;
    border-radius: 28px;
    overflow: hidden;
    background: var(--card-light);
    box-shadow: 0 10px 30px rgba(0,0,0,0.12);
  }
  .brand-panel {
    position: absolute;
    left: 0; top: 0;
    width: 490px;
    height: 100%;
    background: radial-gradient(ellipse at 30% 35%, var(--navy-mid) 0%, var(--navy-deep) 80%);
    display: flex;
    align-items: center;
    justify-content: center;
  }
  .brand-panel::after {
    content: "";
    position: absolute;
    right: 0; top: 0;
    width: 5px;
    height: 100%;
    background: var(--ochre);
  }
  .brand-mark {
    display: flex;
    align-items: center;
    gap: 16px;
    margin-right: 20px;
  }
  .brand-dot {
    width: 18px;
    height: 18px;
    border-radius: 50%;
    background: var(--ochre);
  }
  .brand-name {
    color: var(--white);
    font-weight: 700;
    font-size: 44px;
    letter-spacing: 1px;
  }
  .contact-panel {
    position: absolute;
    left: 567px;
    top: 118px;
    color: var(--body-text);
  }
  .person-name {
    font-size: 36px;
    font-weight: 700;
    color: var(--navy-text);
    letter-spacing: 0.5px;
    line-height: 1.1;
  }
  .person-role {
    font-size: 27px;
    color: var(--ochre);
    line-height: 1.2;
    margin-bottom: 20px;
  }
  .postal-address {
    font-style: normal;
    font-size: 26px;
    line-height: 1.33;
    margin-bottom: 16px;
  }
  .contact-list { list-style: none; }
  .contact-item {
    display: flex;
    align-items: center;
    font-size: 25px;
    line-height: 34px;
  }
  .contact-icon {
    width: 21px;
    height: 21px;
    margin-right: 13px;
    fill: var(--navy-text);
    flex: none;
  }
</style>
</head>
<body>
  <div class="business-card">
    <div class="brand-panel">
      <div class="brand-mark">
        <span class="brand-dot"></span>
        <span class="brand-name">R&amp;W</span>
      </div>
    </div>
    <div class="contact-panel">
      <h1 class="person-name">DAN MORROW</h1>
      <p class="person-role">CEO/Founder</p>
      <address class="postal-address">14 Ridgeway Road<br>Tennant Creek, NT 0860</address>
      <ul class="contact-list">
        <li class="contact-item">
          <svg class="contact-icon" viewBox="0 0 24 24" aria-hidden="true"><path d="M6.6 10.8a15.1 15.1 0 0 0 6.6 6.6l2.2-2.2c.3-.3.7-.4 1-.2 1.1.4 2.3.6 3.6.6.6 0 1 .4 1 1V20c0 .6-.4 1-1 1A17 17 0 0 1 3 4c0-.6.4-1 1-1h3.5c.6 0 1 .4 1 1 0 1.3.2 2.5.6 3.6.1.3 0 .7-.2 1z"/></svg>
          618 204 7731
        </li>
        <li class="contact-item">
          <svg class="contact-icon" viewBox="0 0 24 24" aria-hidden="true"><path d="M6 2h9l3 3v4H6z M3 10h18a1 1 0 0 1 1 1v8a1 1 0 0 1-1 1H3a1 1 0 0 1-1-1v-8a1 1 0 0 1 1-1z M6 16h12v2H6z"/></svg>
          618 204 7739
        </li>
        <li class="contact-item">
          <svg class="contact-icon" viewBox="0 0 24 24" aria-hidden="true"><path d="M2 5h20v14H2z" /><path d="M2 5l10 8 10-8" fill="none" stroke="#f1f2f3" stroke-width="1.8"/></svg>
          mail@rwgroup.com
        </li>
        <li class="contact-item">
          <svg class="contact-icon" viewBox="0 0 24 24" aria-hidden="true"><circle cx="12" cy="12" r="10"/><path d="M2 12h20M12 2c3 3 3 17 0 20M12 2c-3 3-3 17 0 20" fill="none" stroke="#f1f2f3" stroke-width="1.5"/></svg>
          www.rwgroup.com
        </li>
      </ul>
    </div>
  </div>
</body>
</html>
```